Criação de Layout de site para Computador & Internet
A empresa queria:
" Provedor de Internet banda larga para pessoas físicas e jurídicas com cobertura em duas cidades na região dos lagos, no Rio de Janeiro. "

```html
<!DOCTYPE html>
<html lang="pt-BR">
<head>
<meta charset="utf-8">
<title>Conecta Lagos — Banda larga</title>
<link href="https://fonts.googleapis.com/css2?family=Montserrat:wght@400;600;700&display=swap" rel="stylesheet">
<style>
  :root{
    --stage:#d9d9d9;
    --page:#ececec;
    --orange:#f07c1c;
    --orange-dark:#d9620c;
    --orange-deep:#b94f08;
    --card:rgba(120,45,0,.22);
    --white:#ffffff;
    --cream:#ffe6d2;
  }
  *{box-sizing:border-box;margin:0;padding:0}
  html,body{width:1200px;height:1200px;overflow:hidden}
  body{background:var(--stage);font-family:"Montserrat",Arial,sans-serif;position:relative}
  .site{position:absolute;left:0;top:259px;width:1200px;height:682px;background:var(--page);overflow:visible}
  .headline{position:absolute;top:62px;left:0;width:100%;text-align:center;color:var(--orange);font-weight:700;font-size:26px}
  .band{position:absolute;left:0;top:136px;width:100%;height:404px;
    background:linear-gradient(90deg,var(--orange-dark) 0%,var(--orange) 45%,var(--orange) 100%)}
  .band-photo{position:absolute;left:380px;top:0;width:520px;height:404px;
    background:linear-gradient(120deg,rgba(255,255,255,0) 0%,rgba(120,40,0,.18) 50%,rgba(255,255,255,0) 100%)}
  .features{position:absolute;left:77px;top:58px;display:grid;grid-template-columns:262px 262px;column-gap:24px;row-gap:22px}
  .feature{display:flex;gap:12px;align-items:flex-start;background:var(--card);border-radius:10px;padding:12px 12px;height:92px}
  .feature-icon{flex:0 0 46px;height:46px;border-radius:50%;background:var(--white);display:flex;align-items:center;justify-content:center}
  .feature-icon svg{width:24px;height:24px;fill:none;stroke:var(--orange);stroke-width:2.2;stroke-linecap:round;stroke-linejoin:round}
  .feature h3{color:var(--white);font-size:11.5px;font-weight:700;margin-bottom:4px}
  .feature p{color:var(--cream);font-size:10px;line-height:1.35;font-weight:400}
  .hero-photo{position:absolute;left:650px;top:209px;width:485px;height:383px;border-radius:14px;
    background:radial-gradient(ellipse at 45% 40%,#f5c623 0%,#f2a31c 40%,#e07a16 70%,rgba(90,90,90,.55) 100%)}
</style>
</head>
<body>
<main class="site">
  <h2 class="headline">Com a gente você terá o melhor serviço da região.</h2>
  <section class="band">
    <div class="band-photo" role="img" aria-label="Foto esmaecida de mãos usando um notebook"></div>
    <div class="features">
      <div class="feature">
        <div class="feature-icon"><svg viewBox="0 0 24 24"><path d="M13 2 5 14h6l-1 8 8-12h-6z"/></svg></div>
        <div><h3>Internet mais rápida da região</h3><p>A Conecta Lagos é o provedor de Internet mais rápido da Região.</p></div>
      </div>
      <div class="feature">
        <div class="feature-icon"><svg viewBox="0 0 24 24"><rect x="3" y="4" width="18" height="12" rx="1.5"/><path d="M8 20h8M12 16v4"/></svg></div>
        <div><h3>Rede Monitorada</h3><p>Monitoramos a rede 24 horas por dia, 7 dias por semana.</p></div>
      </div>
      <div class="feature">
        <div class="feature-icon"><svg viewBox="0 0 24 24"><path d="M4 14v-2a8 8 0 0 1 16 0v2"/><rect x="3" y="13" width="4" height="6" rx="1"/><rect x="17" y="13" width="4" height="6" rx="1"/></svg></div>
        <div><h3>Suporte Técnico</h3><p>Qualidade e agilidade no atendimento todos os dias de 08:00 às 00:00, inclusive domingos e feriados.</p></div>
      </div>
      <div class="feature">
        <div class="feature-icon"><svg viewBox="0 0 24 24"><rect x="3" y="7" width="13" height="11" rx="1.5"/><path d="m16 11 5-3v9l-5-3"/></svg></div>
        <div><h3>Séries, filmes e muito mais!</h3><p>Com a Conecta Lagos você tem acesso a uma conexão estável com muito mais velocidade e estabilidade.</p></div>
      </div>
      <div class="feature">
        <div class="feature-icon"><svg viewBox="0 0 24 24"><path d="M12 3c4 3 5 8 3 13H9C7 11 8 6 12 3z"/><path d="M9 16l-3 4M15 16l3 4"/><circle cx="12" cy="9" r="1.5"/></svg></div>
        <div><h3>Sem limites</h3><p>Não existe qualquer tipo de franquia limitando o uso da Internet.</p></div>
      </div>
      <div class="feature">
        <div class="feature-icon"><svg viewBox="0 0 24 24"><path d="M4 5h16v10H9l-5 4z"/></svg></div>
        <div><h3>Melhor Atendimento</h3><p>A equipe Conecta Lagos está sempre pronta para te ajudar, sem enrolação, pertinho de você.</p></div>
      </div>
    </div>
  </section>
  <div class="hero-photo" role="img" aria-label="Homem sorridente saindo da tela de um notebook, apontando para cima, cercado de ícones de entretenimento e anéis de luz"></div>
</main>
</body>
</html>
```